Print materials for 3-star hotel

We are changing up our print materials (notepads, letterheads, key card jackets, small flyer for the room rates) We are a 3 star business hotel in the Philippines and have mainly used grey tones and clean, simple lines. See attached photos for logo and hotel interior photos.

Target Market(s)

Business

Contact Information for Business Card

Corvale Terrace Hotel
Lindwell Banca Avenue corner Tolenta St Cebu City 6000 Philippines
Tel: +63 32 481 7302
Mobile: +63 917 648 2095
www.corvaleterracehotel.example

Font styles to use
Serif
Sans Serif

Requirements
Must have
• Simple
• Readable font and font size
Nice to have
• Neutral colors, grey and taupes
Should not have
• No purples and bright blues

```html
<!DOCTYPE html>
<html lang="en">
<head>
<meta charset="utf-8">
<title>Corvale Terrace Hotel — Business Card</title>
<link rel="stylesheet" href="https://fonts.googleapis.com/css2?family=Open+Sans:wght@400;600;700&family=Cormorant+Garamond:wght@500&display=swap">
<style>
  :root {
    --backdrop: #232323;
    --card: #141414;
    --card-edge: #2a2a2a;
    --ink: #f2f2f2;
    --ink-soft: #c9c9c9;
    --silver: #bdbdbd;
    --rule: #8a8a8a;
  }
  * { margin: 0; padding: 0; box-sizing: border-box; }
  html, body {
    width: 1200px; height: 1017px; overflow: hidden;
    background: var(--backdrop);
    font-family: "Open Sans", Arial, sans-serif;
  }
  .canvas { position: relative; width: 1200px; height: 1017px; }

  .card {
    position: absolute;
    width: 560px; height: 320px;
    background: var(--card);
    border: 1px solid var(--card-edge);
    box-shadow: 0 24px 48px rgba(0,0,0,0.45);
  }
  .card--front { left: 70px; top: 150px; }
  .card--back  { left: 570px; top: 540px; }

  /* Front */
  .front-mark {
    position: absolute; left: 0; right: 0; top: 108px;
    display: flex; align-items: center; justify-content: center; gap: 14px;
  }
  .mark-square { width: 22px; height: 22px; background: var(--ink); flex: none; }
  .front-name {
    color: var(--ink); font-weight: 600; font-size: 24px;
    letter-spacing: 5px; text-transform: uppercase;
  }
  .front-url {
    position: absolute; left: 0; right: 0; bottom: 58px;
    text-align: center; color: var(--ink);
    font-size: 15px; letter-spacing: 4px;
  }

  /* Back */
  .back-brand {
    position: absolute; left: 30px; top: 118px; width: 236px;
    display: flex; flex-direction: column; align-items: center; gap: 10px;
  }
  .back-brand .mark-square { width: 20px; height: 20px; background: var(--silver); }
  .brand-name {
    color: var(--silver); font-family: "Cormorant Garamond", Georgia, serif;
    font-weight: 500; font-size: 19px;
    letter-spacing: 4px; text-transform: uppercase; text-align: center; line-height: 1.35;
  }
  .divider { position: absolute; left: 285px; top: 30px; }
  .contact {
    position: absolute; left: 308px; top: 40px; width: 240px;
    color: var(--ink-soft); font-size: 11.5px; line-height: 1.6;
  }
  .contact-name { color: var(--ink); font-weight: 700; font-size: 17px; letter-spacing: 0.5px; line-height: 1.2; }
  .contact-role { color: var(--ink); font-size: 11px; letter-spacing: 1px; margin-bottom: 10px; }
  .contact-line { white-space: nowrap; }
</style>
</head>
<body>
<main class="canvas">
  <section class="card card--front" aria-label="Business card front">
    <div class="front-mark">
      <span class="mark-square"></span>
      <span class="front-name">Corvale Terrace Hotel</span>
    </div>
    <p class="front-url">www.corvaleterracehotel.example</p>
  </section>

  <section class="card card--back" aria-label="Business card back">
    <div class="back-brand">
      <span class="mark-square"></span>
      <span class="brand-name">Corvale Terrace<br>Hotel</span>
    </div>
    <svg class="divider" width="2" height="260" viewBox="0 0 2 260" aria-hidden="true">
      <defs>
        <linearGradient id="rule-fade" x1="0" y1="0" x2="0" y2="1">
          <stop offset="0" stop-color="#8a8a8a" stop-opacity="0.9"/>
          <stop offset="1" stop-color="#8a8a8a" stop-opacity="0"/>
        </linearGradient>
      </defs>
      <rect x="0" y="0" width="1" height="260" fill="url(#rule-fade)"/>
    </svg>
    <div class="contact">
      <p class="contact-name">ELIAS MORENO</p>
      <p class="contact-role">PRESIDENT</p>
      <p class="contact-line">Lindwell Banca Avenue</p>
      <p class="contact-line">corner Tolenta St, Cebu City 6000</p>
      <p class="contact-line">Philippines</p>
      <p class="contact-line">(T) +63 32 481 7302</p>
      <p class="contact-line">(M) +63 917 648 2095</p>
      <p class="contact-line">elias@corvaleterracehotel.example</p>
      <p class="contact-line">www.corvaleterracehotel.example</p>
    </div>
  </section>
</main>
</body>
</html>
```